Realty Group Needs Classy, Contemporary Letterhead Design

We need a letterhead design for a new realty company located in NY, USA. We buy investment properties to rehabilitate and or keep in our rental portfolio.

```html
<!DOCTYPE html>
<html lang="en">
<head>
<meta charset="utf-8">
<title>Meridian Realty Group Letterhead</title>
<link href="https://fonts.googleapis.com/css2?family=Arimo:wght@400;700&display=swap" rel="stylesheet">
<style>
  :root {
    --brand: #4f2d8a;
    --ink: #2b2b2b;
    --rule: #8a8a8a;
    --backdrop: #e9e9eb;
    --paper: #ffffff;
    --signature-tone: #d9d6e0;
  }
  * { margin: 0; padding: 0; box-sizing: border-box; }
  html, body { width: 1200px; height: 874px; overflow: hidden; }
  body {
    background: var(--backdrop);
    font-family: "Arimo", Arial, sans-serif;
    color: var(--ink);
    position: relative;
  }
  .letterhead {
    position: absolute;
    left: 305px; top: 20px;
    width: 590px; height: 834px;
    background: var(--paper);
    box-shadow: 0 4px 18px rgba(0,0,0,.12);
    display: flex; flex-direction: column;
  }
  .masthead {
    padding-top: 58px;
    display: flex; flex-direction: column; align-items: center;
  }
  .company-name {
    font-weight: 700; font-size: 27px; color: var(--brand);
    letter-spacing: .5px;
  }
  .masthead-rule {
    margin-top: 10px; width: 260px; height: 1px; background: var(--rule);
  }
  .letter {
    padding: 70px 62px 0 70px;
    font-size: 10.5px; line-height: 1.5;
  }
  .recipient { margin-bottom: 14px; }
  .letter p { margin-bottom: 16px; }
  .closing { margin-top: 6px; }
  .signature {
    margin-top: 12px; width: 150px; height: 46px;
    background: var(--signature-tone); border-radius: 3px;
  }
  .footer { margin-top: auto; }
  .footer-rule { height: 1px; background: var(--rule); margin: 0 30px; }
  .contact-row {
    display: flex; align-items: center; justify-content: space-between;
    padding: 14px 44px; font-size: 11px; line-height: 1.6;
  }
  .contact-item { display: flex; align-items: center; gap: 7px; white-space: nowrap; }
  .contact-item svg { width: 10px; height: 10px; fill: var(--brand); flex: none; }
  .contact-divider { width: 2px; height: 28px; background: var(--rule); }
  .contact-address { white-space: nowrap; }
  .brand-band { height: 14px; background: var(--brand); margin-top: 22px; }
</style>
</head>
<body>
  <article class="letterhead">
    <header class="masthead">
      <div class="company-name">Meridian Realty Group, LLC</div>
      <div class="masthead-rule"></div>
    </header>

    <section class="letter">
      <div class="recipient">
        Mr/s<br>First Name and Last Name<br>Company Name<br>Address
      </div>
      <p>Lorem Ipsum is simply dummy text of the printing and typesetting industry. Lorem Ipsum has been the industry's standard dummy text ever since the 1500s, when an unknown printer took a galley of type and scrambled it to make a type specimen book. It has survived not only five centuries, but also the leap into electronic typesetting, remaining essentially unchanged. It was popularised in the 1960s with the release of Letraset sheets containing Lorem Ipsum passages.</p>
      <p>The standard chunk of Lorem Ipsum used since the 1500s is reproduced below for those interested. Sections 1.10.32 and 1.10.33 from "de Finibus Bonorum et Malorum" by Cicero are also reproduced in their exact original form, accompanied by English versions from the 1914 translation by H. Rackham. Lorem ipsum dolor sit amet, consectetur adipiscing elit, sed do eiusmod tempor incididunt ut labore et dolore magna aliqua.</p>
      <p>It is a long established fact that a reader will be distracted by the readable content of a page when looking at its layout. The point of using Lorem Ipsum is that it has a more-or-less normal distribution of letters, as opposed to using 'Content here, content here', making it look like readable English. Many desktop publishing packages and web page editors now.</p>
      <div class="closing">Your Sincerely,</div>
      <div class="signature" role="img" aria-label="Handwritten signature"></div>
    </section>

    <footer class="footer">
      <div class="footer-rule"></div>
      <div class="contact-row">
        <div>
          <div class="contact-item">
            <svg viewBox="0 0 10 10"><path d="M2 0.5l2 2-1 1.2c.6 1.3 1.6 2.3 2.9 2.9l1.2-1 2 2-1.3 1.9C4.5 9 1 5.5.6 1.8z"/></svg>
            555-208-3174
          </div>
          <div class="contact-item">
            <svg viewBox="0 0 10 10"><rect x="2.5" y="0.5" width="5" height="3"/><rect x="0.5" y="3.5" width="9" height="4" rx="1"/><rect x="2.5" y="6.5" width="5" height="3"/></svg>
            555-208-3190
          </div>
        </div>
        <div class="contact-divider"></div>
        <div>
          <div class="contact-item">
            <svg viewBox="0 0 10 10"><path d="M0 2h10v6H0z M0 2l5 3.5L10 2" fill="none" stroke="#4f2d8a" stroke-width="1.3"/></svg>
            info@meridianrealtyllc.com
          </div>
          <div class="contact-item">
            <svg viewBox="0 0 10 10"><circle cx="5" cy="5" r="4.3" fill="none" stroke="#4f2d8a" stroke-width="1.2"/><path d="M0.7 5h8.6M5 0.7c-2.2 2.5-2.2 6.1 0 8.6M5 0.7c2.2 2.5 2.2 6.1 0 8.6" fill="none" stroke="#4f2d8a" stroke-width="0.9"/></svg>
            www.meridianrealtyllc.com
          </div>
        </div>
        <div class="contact-divider"></div>
        <div class="contact-address">2270 Harbor View Road, Suite<br>310 Name, NY, USA</div>
      </div>
      <div class="footer-rule"></div>
      <div class="brand-band"></div>
    </footer>
  </article>
</body>
</html>
```